LLC needs a business card design that emphasizes consulting and expert witness in upstream oil and g

I need a business card design for my company called Obena Consultative Service, LLC. My expertise is in oil and gas upstream operations management to optimize performance and also as an expert witness for law firms in oil and gas upstream operations litigation.
The final design should communicate knowledge and hands-on experience as well as trust. (Obena means rope or lasso. Perhaps "Obena" should be in the form of a rope.) I do not like the color green in any shade. My first preference would be some shade of blue.
Industry/Entity Type
Oil And Gas

```html
<!DOCTYPE html>
<html lang="en">
<head>
<meta charset="utf-8">
<title>Obena Consultative Service, LLC – Business Card</title>
<link href="https://fonts.googleapis.com/css2?family=Marcellus&family=Arimo:wght@400&display=swap" rel="stylesheet">
<style>
  :root {
    --page-bg: #e9e7e3;
    --card-bg: #ffffff;
    --card-shade: #f1f1f1;
    --brand-blue: #1f5fa8;
    --brand-red: #b3171b;
    --brand-red-dark: #8f1013;
    --text-white: #ffffff;
  }
  * { margin: 0; padding: 0; box-sizing: border-box; }
  html, body { width: 1200px; height: 892px; overflow: hidden; }
  body {
    background: var(--page-bg);
    position: relative;
    font-family: "Arimo", Arial, sans-serif;
  }
  .card {
    position: absolute;
    top: 292px;
    width: 540px;
    height: 309px;
    background: linear-gradient(160deg, var(--card-bg) 55%, var(--card-shade));
    box-shadow: 0 6px 18px rgba(0,0,0,0.18);
    overflow: hidden;
  }
  .card--front { left: 40px; }
  .card--back { left: 620px; }

  .company-name {
    font-family: "Marcellus", Georgia, serif;
    color: var(--brand-blue);
    white-space: nowrap;
  }
  .card--front .company-name {
    position: absolute;
    left: 28px;
    top: 70px;
    font-size: 25px;
    display: flex;
    align-items: center;
    gap: 10px;
  }
  .brand-dot {
    width: 12px; height: 12px;
    border-radius: 50%;
    background: var(--brand-red);
    flex: none;
  }
  .divider {
    position: absolute;
    left: 318px;
    top: 112px;
    width: 1px;
    height: 72px;
    background: var(--brand-red);
  }
  .person {
    position: absolute;
    left: 338px;
    top: 122px;
    color: var(--brand-blue);
  }
  .person-name { font-size: 27px; line-height: 1.1; }
  .person-title { font-size: 12px; margin-top: 4px; }

  .contacts {
    position: absolute;
    left: 30px;
    top: 160px;
    list-style: none;
    color: var(--brand-blue);
    font-size: 13px;
    line-height: 18px;
  }
  .contacts li { display: flex; align-items: center; gap: 10px; }
  .contacts svg { width: 11px; height: 11px; flex: none; }

  .address-band {
    position: absolute;
    left: 0; right: 0; bottom: 0;
    height: 56px;
    background: linear-gradient(180deg, var(--brand-red), var(--brand-red-dark));
    color: var(--text-white);
    font-size: 14px;
    letter-spacing: 0.2px;
    display: flex;
    align-items: center;
    padding-left: 60px;
  }

  .card--back {
    display: flex;
    align-items: center;
    justify-content: center;
  }
  .card--back .company-name {
    font-size: 31px;
    display: flex;
    align-items: center;
    gap: 12px;
  }
  .card--back .brand-dot { width: 16px; height: 16px; }
</style>
</head>
<body>

<section class="card card--front" aria-label="Card front">
  <div class="company-name"><span class="brand-dot"></span>Obena Consultative Service, LLC</div>

  <ul class="contacts">
    <li>
      <svg viewBox="0 0 12 12"><path d="M2.5 1 L4.5 1 L5.2 3.6 L4 4.6 Q5 7 7.4 8 L8.4 6.8 L11 7.5 L11 9.5 Q10.5 11 9 11 Q1 10 1 3 Q1 1.5 2.5 1 Z" fill="var(--brand-red)"/></svg>
      036-4107 2290
    </li>
    <li>
      <svg viewBox="0 0 12 12"><rect x="1.5" y="2" width="9" height="8" rx="1" fill="none" stroke="var(--brand-red)" stroke-width="1.2"/></svg>
      123-5530 7841
    </li>
    <li>
      <svg viewBox="0 0 12 12"><rect x="1" y="2.5" width="10" height="7" fill="var(--brand-red)"/><path d="M1 2.5 L6 6.5 L11 2.5" fill="none" stroke="#fff" stroke-width="1"/></svg>
      info@obenaconsult.com
    </li>
    <li>
      <svg viewBox="0 0 12 12"><circle cx="6" cy="6" r="5" fill="var(--brand-red)"/><path d="M1 6 H11 M6 1 Q3 6 6 11 M6 1 Q9 6 6 11" fill="none" stroke="#fff" stroke-width="0.8"/></svg>
      www.obenaconsult.com
    </li>
  </ul>

  <div class="divider"></div>

  <div class="person">
    <div class="person-name">Employee name</div>
    <div class="person-title">Managing Director</div>
  </div>

  <div class="address-band">Your Address Inc 4th Ridge Ave Tulsa,OK 00000</div>
</section>

<section class="card card--back" aria-label="Card back">
  <div class="company-name"><span class="brand-dot"></span>Obena Consultative Service, LLC</div>
</section>

</body>
</html>
```